Awesome business card design needed

We need a new business card design to go with our new logo.
We are a web development agency that specialises in highly complex back-end integrations as opposed to design, our customers are retailers, hotels, hospitals and any other organisation that has a large online marketing department.
Take a look at our website - www.brenoloft.com for some inspiration.
We want our new business cards to exude class, professionalism and style.
We are likely to choose a high-end card to print them on but we want the design of the card itself to really turn heads.
We have no specific colour requirements, the logo as you will see is a turquoise colour R89 G171 B167 #59aba7 but it can also be in white if you want to make the colour of the card something different.
The information on the card should be:
Name
Position
Tel
email
Potentially a double sided card could have our web address, twitter and FB links.

```html
<!DOCTYPE html>
<html lang="en">
<head>
<meta charset="utf-8">
<title>Brenoloft Business Card</title>
<link rel="stylesheet" href="https://fonts.googleapis.com/css2?family=Play:wght@400;700&display=swap">
<style>
  :root {
    --page: #ecebe8;
    --card-top: #e9dcc0;
    --teal: #59aba7;
    --band: #2e2e2e;
    --white: #ffffff;
  }
  * { margin: 0; padding: 0; box-sizing: border-box; }
  html, body { width: 1200px; height: 1197px; overflow: hidden; }
  body {
    background: var(--page);
    font-family: "Play", sans-serif;
    position: relative;
  }
  .card {
    position: absolute;
    width: 663px;
    height: 379px;
    border-radius: 28px;
    overflow: hidden;
    background: var(--card-top);
    box-shadow: 0 6px 18px rgba(0,0,0,0.12);
  }
  .card-front { left: 97px; top: 164px; }
  .card-back { left: 421px; top: 669px; }
  .card-shape { position: absolute; inset: 0; width: 100%; height: 100%; }
  .wordmark {
    position: absolute;
    left: 0; right: 0;
    top: 38px;
    text-align: center;
    font-weight: 700;
    font-size: 104px;
    line-height: 1;
    color: var(--teal);
    letter-spacing: 2px;
  }
  .details {
    position: absolute;
    left: 0; right: 0;
    top: 232px;
    text-align: center;
    color: var(--white);
  }
  .person { font-size: 22px; line-height: 1; }
  .person .name { font-weight: 700; }
  .person .position { font-size: 18px; }
  .phone { font-size: 19px; margin-top: 14px; line-height: 1; }
  .contact-line { font-size: 17px; margin-top: 9px; line-height: 1; display: flex; justify-content: center; align-items: center; gap: 6px; }
  .contact-line svg { width: 13px; height: 13px; }
  .address { font-size: 18px; margin-top: 18px; line-height: 1; }
  .follow {
    position: absolute;
    left: 0; right: 0;
    top: 278px;
    display: flex;
    justify-content: center;
    align-items: center;
    gap: 10px;
    color: var(--white);
    font-weight: 700;
    font-size: 23px;
    letter-spacing: 0.5px;
  }
  .social-square {
    width: 36px; height: 36px;
    border-radius: 6px;
    background: #4a8fd0;
  }
  .social-square.second { background: #3b5a9a; }
  .web {
    position: absolute;
    left: 0; right: 0;
    top: 329px;
    text-align: center;
    color: var(--white);
    font-size: 20px;
    letter-spacing: 2px;
  }
  .web b { font-weight: 700; }
</style>
</head>
<body>

<section class="card card-front">
  <svg class="card-shape" viewBox="0 0 663 379" preserveAspectRatio="none" aria-hidden="true">
    <path d="M0 150 Q330 262 663 156 L663 379 L0 379 Z" fill="var(--band)"/>
    <path d="M0 164 Q330 274 663 168 L663 379 L0 379 Z" fill="var(--teal)"/>
  </svg>
  <div class="wordmark">brenoloft</div>
  <div class="details">
    <p class="person"><span class="name">Your Name,</span> <span class="position">Position</span></p>
    <p class="phone">&#9990; 123-456-7890</p>
    <p class="contact-line">
      <svg viewBox="0 0 14 14"><rect x="1" y="3" width="12" height="8" fill="none" stroke="#fff" stroke-width="1.6"/><path d="M1 3 L7 8 L13 3" fill="none" stroke="#fff" stroke-width="1.6"/></svg>
      info@brenoloft.com
      <svg viewBox="0 0 14 14"><circle cx="7" cy="7" r="6" fill="none" stroke="#fff" stroke-width="1.5"/><path d="M1 7 H13 M7 1 Q3 7 7 13 M7 1 Q11 7 7 13" fill="none" stroke="#fff" stroke-width="1.2"/></svg>
      www.brenoloft.com
    </p>
    <p class="address">Street Name, City Name, State Zip Code</p>
  </div>
</section>

<section class="card card-back">
  <svg class="card-shape" viewBox="0 0 663 379" preserveAspectRatio="none" aria-hidden="true">
    <path d="M0 152 Q330 262 663 156 L663 379 L0 379 Z" fill="var(--band)"/>
    <path d="M0 166 Q330 274 663 168 L663 379 L0 379 Z" fill="var(--teal)"/>
  </svg>
  <div class="wordmark">brenoloft</div>
  <div class="follow">
    <span>Follow Us On:</span>
    <span class="social-square"></span>
    <span class="social-square second"></span>
  </div>
  <p class="web">www.<b>brenoloft</b>.com</p>
</section>

</body>
</html>
```